creative menu design for a fun taco restaurant

menu design for taco restaurant.
graphically creative. handwritten edgy style.
logo with current writing attached.
--for creative inspiration similar to what I am looking for go to :
Glimmaro -- Colin fairway @ridgeway482 -taco menu board
menu has create your own taco and burrito
and a cocktail/ beer menu
1970's inspired. should be FUN

Target Market(s)

20-40 milliners and gen z

Colors
f37022
9bcb3c
fbed22
1196d0
ec1f27

Requirements
Must have
• colorful
images
playful/ fun--it's TACOS
Nice to have
• graphics, handwritten, use of colors, 1970's-60's font
Should not have
• slick food photos
faded photos drawings are ok

```html
<!DOCTYPE html>
<html lang="en">
<head>
<meta charset="utf-8">
<title>Sassy Tortilla – Menu</title>
<link rel="stylesheet" href="https://fonts.googleapis.com/css2?family=Chango&family=Oswald:wght@300;400&family=Shrikhand&family=Sriracha&family=Titan+One&display=swap">
<style>
:root{
  --purple:#5b2a6e;
  --orange:#f37022;
  --green:#9bcb3c;
  --yellow:#fbed22;
  --blue:#1196d0;
  --red:#ec1f27;
  --pink:#e8457c;
  --teal:#a3dbd8;
  --aqua:#1bb5a8;
  --white:#ffffff;
}
*{margin:0;padding:0;box-sizing:border-box}
html,body{width:1200px;height:2567px;overflow:hidden;background:var(--white)}
body{position:relative;font-family:'Oswald',sans-serif;font-weight:300;color:var(--purple)}
.panel{position:absolute;width:585px;overflow:hidden;background:var(--white)}
.col-left{left:0}
.col-right{left:619px}
.row-1{top:0;height:817px}
.row-2{top:868px;height:818px}
.row-3{top:1757px;height:810px}
.band{position:absolute;left:0;width:100%;background:linear-gradient(180deg,var(--aqua) 0%,var(--yellow) 25%,var(--pink) 50%,var(--orange) 70%,var(--purple) 100%)}
.band-top{top:0;height:88px}
.band-bottom{bottom:0;height:90px;transform:scaleY(-1)}
.art{position:absolute;border-radius:50%}
.flower{width:40px;height:40px;background:radial-gradient(circle,var(--yellow) 0 20%,var(--blue) 21% 45%,var(--red) 46%);border-radius:50%}
.cover{background:var(--teal)}
.brand{position:absolute;left:0;width:100%;top:300px;text-align:center;font-family:'Shrikhand',cursive;font-size:58px;color:var(--orange)}
.brand-dot{position:absolute;left:262px;top:190px;width:62px;height:62px;border-radius:50%;background:var(--pink)}
.script{font-family:'Sriracha',cursive;color:var(--pink);white-space:nowrap}
.center{position:absolute;left:0;width:100%;text-align:center}
.spaced{font-family:'Titan One',cursive;letter-spacing:.28em;color:var(--purple)}
.section-title{position:absolute;left:0;width:100%;text-align:center;font-family:'Chango',cursive;font-size:26px;letter-spacing:.06em}
.section-title.plain{font-family:'Titan One',cursive;letter-spacing:.1em}
.subhead{font-family:'Titan One',cursive;font-size:10px;letter-spacing:.3em;color:var(--purple)}
.note{font-size:12px;color:var(--orange);line-height:1.15}
.item{position:absolute}
.line{display:flex;align-items:baseline;gap:4px}
.stack .line{line-height:18px}
.name{font-family:'Titan One',cursive;font-size:15px;color:var(--purple);white-space:nowrap;letter-spacing:.01em}
.rule{flex:1;border-bottom:1px solid var(--purple);transform:translateY(-4px)}
.price{font-family:'Oswald',sans-serif;font-weight:400;font-size:15px;color:var(--purple);white-space:nowrap}
.desc{font-size:11.5px;color:var(--orange);line-height:1.2}
.extra{font-size:11.5px;color:var(--purple);text-transform:uppercase;font-weight:400}
.c-o{color:var(--orange)}.c-g{color:var(--green)}.c-y{color:#e8c400}.c-b{color:var(--blue)}.c-r{color:var(--red)}.c-p{color:var(--purple)}.c-k{color:var(--pink)}.c-a{color:var(--aqua)}
.desc.c-a{color:var(--aqua)}
</style>
</head>
<body>

<section class="panel col-left row-1 cover">
  <div class="band band-top" role="img" aria-label="Zigzag stripe border in teal, yellow, pink, orange and purple"></div>
  <div class="brand-dot"></div>
  <div class="brand">Sassy Tortilla</div>
  <p class="center script" style="top:566px;font-size:26px">Our tacos are classic Mexican size.</p>
  <p class="center script" style="top:603px;font-size:18px">We recommend one for a snack, and two or three as a main meal</p>
  <p class="center spaced" style="top:644px;font-size:24px">Handmade Corn Tortillas</p>
  <div class="band band-bottom" role="img" aria-label="Zigzag stripe border in teal, yellow, pink, orange and purple"></div>
</section>

<section class="panel col-right row-1">
  <div class="band band-top" role="img" aria-label="Zigzag stripe border"></div>
  <div class="art flower" style="left:86px;top:124px" role="img" aria-label="Paper flower"></div>
  <div class="art flower" style="left:498px;top:102px;width:54px;height:54px" role="img" aria-label="Paper flower"></div>
  <div class="art flower" style="left:450px;top:222px;width:54px;height:54px" role="img" aria-label="Paper flower"></div>
  <h2 class="section-title plain c-p" style="top:112px;font-size:28px">TACOS</h2>
  <p class="center subhead" style="top:150px">HANDMADE CORN TORTILLAS</p>
  <p class="center note" style="top:171px">Our tacos are classic Mexican size. We recommend one for<br>a snack, and two or three as main meal</p>
  <div class="art" style="left:226px;top:215px;width:140px;height:85px;border-radius:70px 70px 20px 20px;background:linear-gradient(160deg,var(--green),var(--yellow) 50%,var(--orange))" role="img" aria-label="Illustrated taco with lettuce, tomato and cheese"></div>

  <div class="item" style="left:90px;width:412px;top:314px"><div class="line"><span class="name">Vegan Taco</span><span class="rule"></span><span class="price">40</span></div><p class="desc">Seasonal vegetables, quinoa, black beans, corn, pipian sauce</p></div>
  <div class="item" style="left:90px;width:412px;top:353px"><div class="line"><span class="name">Vegetarian Taco</span><span class="rule"></span><span class="price">50</span></div><p class="desc">Braised chickpeas with goat cheese crema</p></div>
  <div class="item" style="left:90px;width:412px;top:391px"><div class="line"><span class="name">Pork Taco</span><span class="rule"></span><span class="price">50</span></div><p class="desc">Pork carnitas, romesco sauce, queso fresco, almonds, pickled red onion</p></div>
  <div class="item" style="left:90px;width:412px;top:429px"><div class="line"><span class="name">Pork Rib Taco</span><span class="rule"></span><span class="price">55</span></div><p class="desc">Pork rib meat, spicy bbq sauce, red cabbage, iceberg lettuce, sesame</p></div>
  <div class="item" style="left:90px;width:412px;top:468px"><div class="line"><span class="name">Chipotle Chicken Taco</span><span class="rule"></span><span class="price">50</span></div><p class="desc">Roasted chicken, taco slaw, jalapenos</p></div>
  <div class="item" style="left:90px;width:412px;top:507px"><div class="line"><span class="name">Beef Brisket Barbacoa Taco</span><span class="rule"></span><span class="price">60</span></div><p class="desc">Beef brisket barbacoa, queso fresco, picked red, avocado</p></div>
  <div class="item" style="left:90px;width:412px;top:545px"><div class="line"><span class="name">Chopped Cheese Taco</span><span class="rule"></span><span class="price">55</span></div><p class="desc">Minced Aus. beef, onion, chili, cheese, pico de gallo, iceberg lettuce, Casa burger sauce</p></div>
  <div class="item" style="left:90px;width:412px;top:584px"><div class="line"><span class="name">Shrimp Taco</span><span class="rule"></span><span class="price">60</span></div><p class="desc">Shrimp in a spicy diablo tomato sauce</p></div>
  <div class="item" style="left:90px;width:412px;top:622px"><div class="line"><span class="name">Fish Taco</span><span class="rule"></span><span class="price">60</span></div><p class="desc">Red snapper, coconut &amp; peanut salad, cream fraiche</p></div>

  <div class="art" style="left:508px;top:644px;width:72px;height:100px;border-radius:10px;background:linear-gradient(180deg,var(--green),var(--red) 35%,var(--yellow) 60%,var(--blue))" role="img" aria-label="Colourful donkey piñata"></div>
  <p class="script" style="position:absolute;left:125px;top:698px;font-size:10.5px;letter-spacing:.03em">We are happy to accomodate any dietary requirements you may have</p>
  <div class="band band-bottom" role="img" aria-label="Zigzag stripe border"></div>
</section>

<section class="panel col-left row-2">
  <div class="band band-top" role="img" aria-label="Zigzag stripe border"></div>
  <div class="art flower" style="left:50px;top:112px;width:36px;height:36px" role="img" aria-label="Paper flower"></div>
  <h2 class="section-title" style="top:130px"><span class="c-o">S</span><span class="c-r">P</span><span class="c-y">E</span><span class="c-g">C</span><span class="c-b">I</span><span class="c-o">A</span><span class="c-r">L</span><span class="c-y">S</span></h2>

  <div class="item" style="left:85px;width:413px;top:181px"><div class="line"><span class="name">Queso Fundido</span><span class="rule"></span><span class="price">90</span></div><p class="desc" style="width:310px">House-made chorizo, cream, chedder &amp; mozzarella cheese. Served with tortilla chips, pico de gallo and jalapenos. (Vegetarian option available)</p><p class="extra">Extra jalapenos +10</p></div>
  <div class="item" style="left:85px;width:413px;top:258px"><div class="line"><span class="name">Shrimp and Bacon</span><span class="rule"></span><span class="price">150</span></div><p class="desc">Shrimps &amp; becon in a spicy tomato &amp; coconut sauce.</p><p class="desc" style="color:var(--purple)">Served with corn chips</p></div>
  <div class="item" style="left:85px;width:413px;top:309px"><div class="line"><span class="name">Enchiladas <span style="font-family:'Oswald',sans-serif;font-size:11px">* Longer waiting time</span></span><span class="rule"></span><span class="price">150</span></div><p class="desc">Two rolled corn tortillas stuffed with cheese, corn &amp; your choice of filling.</p><p class="desc" style="color:var(--purple)">Served with spicy tomato sauce, melted cheese and onions.</p></div>
  <div class="item stack" style="left:85px;width:170px;top:368px"><div class="line"><span class="name">Vegetable</span><span class="rule"></span><span class="price">115</span></div><div class="line"><span class="name">Pork</span><span class="rule"></span><span class="price">130</span></div><div class="line"><span class="name">Shrimp</span><span class="rule"></span><span class="price">145</span></div></div>
  <div class="item stack" style="left:308px;width:190px;top:368px"><div class="line"><span class="name">Chipotle Chicken</span><span class="rule"></span><span class="price">130</span></div><div class="line"><span class="name">Aus. Beef</span><span class="rule"></span><span class="price">145</span></div></div>

  <div class="art flower" style="left:64px;top:446px;width:44px;height:44px" role="img" aria-label="Paper flower"></div>
  <div class="art flower" style="left:98px;top:492px;width:36px;height:36px" role="img" aria-label="Paper flower"></div>
  <h2 class="section-title" style="top:446px;left:-5px"><span class="c-r">N</span><span class="c-r">A</span><span class="c-o">C</span><span class="c-r">H</span><span class="c-b">O</span><span class="c-r">S</span></h2>
  <p class="center subhead" style="top:483px;left:-5px">WITH FRIED CORN CHIPS</p>
  <p class="center note" style="top:503px;left:0">Served with black beans, mozarella, pico de gallo, jalapenos,<br>pickled red onion &amp; avocado crema.</p>
  <p class="extra" style="position:absolute;left:85px;top:538px;line-height:1.45">Add guacamole +25<br>Extra cheese +20<br>Add sour cream +20</p>
  <div class="item stack" style="left:85px;width:400px;top:598px"><div class="line"><span class="name">Vegetable (pumpkin, corn , pepitas)</span><span class="rule"></span><span class="price">100</span></div><div class="line"><span class="name">Chipotle Chicken</span><span class="rule"></span><span class="price">110</span></div><div class="line"><span class="name">Pork carnitas</span><span class="rule"></span><span class="price">110</span></div><div class="line"><span class="name">Aus. Beef.</span><span class="rule"></span><span class="price">115</span></div></div>
  <p class="script" style="position:absolute;left:131px;top:690px;font-size:13px">Please note we charge an extra 3% for card payments</p>
  <div class="art" style="left:8px;top:682px;width:116px;height:92px;border-radius:50% 50% 20px 20px;background:linear-gradient(180deg,var(--yellow),var(--red) 45%,var(--aqua))" role="img" aria-label="Bowl of salsa with tortilla chips"></div>
  <div class="art" style="left:462px;top:676px;width:108px;height:60px;border-radius:40px;background:linear-gradient(135deg,var(--orange),var(--green) 50%,var(--red))" role="img" aria-label="Pair of maracas"></div>
  <div class="band band-bottom" role="img" aria-label="Zigzag stripe border"></div>
</section>

<section class="panel col-right row-2">
  <div class="band band-top" role="img" aria-label="Zigzag stripe border"></div>
  <div class="art flower" style="left:50px;top:126px;width:44px;height:44px" role="img" aria-label="Paper flower"></div>
  <h2 class="section-title" style="top:138px;left:-2px"><span class="c-r">Q</span><span class="c-o">U</span><span class="c-y">E</span><span class="c-b">S</span><span class="c-g">A</span><span class="c-o">D</span><span class="c-r">I</span><span class="c-y">L</span><span class="c-g">L</span><span class="c-b">A</span><span class="c-r">S</span></h2>
  <p class="center subhead" style="top:176px">FRESH WHEAT TORTILLAS</p>
  <div class="extra" style="position:absolute;left:87px;width:413px;top:199px;display:flex;justify-content:space-between"><span>Add sour cream +20</span><span>Extra cheese +20</span><span>Add guacamole +25</span></div>
  <div class="item" style="left:87px;width:412px;top:221px"><div class="line"><span class="name">Vegetable</span><span class="rule"></span><span class="price">135</span></div><p class="desc">Goat cheese, mozzarella, cranberry, spinach, pico de gallo, jalapenos</p></div>
  <div class="item" style="left:87px;width:412px;top:261px"><div class="line"><span class="name">Chipotle Chicken</span><span class="rule"></span><span class="price">135</span></div><p class="desc" style="margin-top:6px">Mozzarella, corn, avocodo crema, pico de gallo, jalapenos.</p></div>
  <div class="item" style="left:87px;width:412px;top:306px"><div class="line"><span class="name">Pork</span><span class="rule"></span><span class="price">135</span></div><p class="desc">Mozzarella, corn, avocado crema, pico de gallo, jalapenos</p></div>
  <div class="item" style="left:87px;width:412px;top:344px"><div class="line"><span class="name">Aus. Beef</span><span class="rule"></span><span class="price">160</span></div><p class="desc">Mozzarella, corn, avocado, crema, pico de gallo, jalapenos</p></div>

  <div class="art flower" style="left:44px;top:400px;width:36px;height:36px" role="img" aria-label="Paper flower"></div>
  <div class="art flower" style="left:82px;top:432px;width:36px;height:36px" role="img" aria-label="Paper flower"></div>
  <h2 class="section-title" style="top:414px"><span class="c-o">B</span><span class="c-r">U</span><span class="c-y">R</span><span class="c-o">R</span><span class="c-b">I</span><span class="c-r">T</span><span class="c-g">O</span><span class="c-b">S</span></h2>
  <p class="center subhead" style="top:452px">FRESH WHEAT TORTILLAS</p>
  <p class="center note" style="top:472px">With Mexican rice, beans, cheese, pico de gallo, jalepenos &amp; sour cream</p>
  <p class="extra" style="position:absolute;left:87px;top:505px;line-height:1.45">Add guacamole +25<br>Extra cheese +20<br>Add sour cream +20</p>
  <div class="item stack" style="left:206px;width:292px;top:496px"><div class="line"><span class="name">Vegetable (pumpkin and cauliflower)</span><span class="price">130</span></div><div class="line"><span class="name">Chipotle Chicken</span><span class="rule"></span><span class="price">145</span></div><div class="line"><span class="name">Pork carnitas</span><span class="rule"></span><span class="price">145</span></div><div class="line"><span class="name">Aus. Beef.</span><span class="rule"></span><span class="price">160</span></div></div>

  <div class="art" style="left:22px;top:560px;width:72px;height:172px;border-radius:36px 36px 8px 8px;background:linear-gradient(180deg,var(--green) 80%,var(--yellow))" role="img" aria-label="Saguaro cactus on sand"></div>
  <p class="center spaced" style="top:618px;font-size:15px;letter-spacing:.2em;padding-left:40px">Now available: Naked Burrito Bowl</p>
  <p class="center script" style="top:640px;font-size:12.5px;padding-left:20px">All the goodness of a regular burrito, served with no tortilla!</p>
  <p class="center note" style="top:662px">-20 from Regular Burrito Price</p>
  <div class="art" style="left:450px;top:664px;width:116px;height:58px;border-radius:60px 30px 60px 30px;background:linear-gradient(135deg,var(--green) 15%,var(--red) 30%)" role="img" aria-label="Red chili peppers"></div>
  <div class="band band-bottom" role="img" aria-label="Zigzag stripe border"></div>
</section>

<section class="panel col-left row-3">
  <div class="band band-top" role="img" aria-label="Zigzag stripe border"></div>
  <div class="art flower" style="left:122px;top:138px;width:36px;height:36px" role="img" aria-label="Paper flower"></div>
  <div class="art flower" style="left:412px;top:183px;width:36px;height:36px" role="img" aria-label="Paper flower"></div>
  <h2 class="section-title c-g" style="top:176px;font-size:22px;padding-right:10px">SMALL PLATES</h2>

  <div class="item" style="left:86px;width:410px;top:226px"><div class="line"><span class="name">Tortilla Chips</span><span class="rule"></span><span class="price">40/80</span></div><p class="desc">Fried corn tortilla chips</p></div>
  <div class="item" style="left:86px;width:410px;top:266px"><div class="line"><span class="name">Pico de Gallo Salsa</span><span class="rule"></span><span class="price">30/60</span></div><p class="desc">Tomato, jicama, onion, chili, cilantro</p></div>
  <div class="item" style="left:86px;width:410px;top:306px"><div class="line"><span class="name">Guacamole</span><span class="rule"></span><span class="price">75/140</span></div><p class="desc">Muddled avocado, pico de gallo, lime</p></div>
  <div class="item" style="left:86px;width:410px;top:346px"><div class="line"><span class="name">Ceviche (with taro chips)</span><span class="rule"></span><span class="price">90/175</span></div><p class="desc">Red snapper, shrimp, mango, avocado, chili, radish, citrus blend</p></div>
  <div class="item" style="left:86px;width:410px;top:385px"><div class="line"><span class="name">Roasted Cauliflower</span><span style="flex:1"></span><span class="price">85</span></div><p class="desc">Cauliflower with golden raisins, ricotta &amp; capers</p></div>
  <div class="item" style="left:86px;width:410px;top:425px"><div class="line"><span class="name">Roasted Potatoes</span><span style="flex:1"></span><span class="price">60</span></div><p class="desc">Finished in serrano chili-butter and thyme</p></div>
  <p class="extra" style="position:absolute;left:86px;top:467px;word-spacing:6px">Mozzarella +10 &nbsp; &nbsp; Jalapenos +10</p>
  <div class="item" style="left:86px;width:410px;top:487px"><div class="line"><span class="name">Vegan Salad</span><span class="rule"></span><span class="price">60/115</span></div><p class="desc">Frisee salad, snow peas, quinoa, avocado,<br>pumpkin seed, pickled shallots &amp; citronelle dressing</p></div>
  <div class="item" style="left:86px;width:410px;top:538px"><div class="line"><span class="name">House Salad</span><span class="rule"></span><span class="price">65/120</span></div><p class="desc">Arugula, mango, fennel, grana padano &amp; balsamic dressing</p></div>

  <div class="art" style="left:40px;top:600px;width:170px;height:128px;border-radius:50% 50% 6px 6px;background:linear-gradient(180deg,var(--pink),#f49ab8 60%,var(--purple))" role="img" aria-label="Three pink flamingos"></div>
  <div class="art flower" style="left:230px;top:604px" role="img" aria-label="Paper flower"></div>
  <div class="art flower" style="left:282px;top:644px" role="img" aria-label="Paper flower"></div>
  <div class="art flower" style="left:225px;top:656px;width:34px;height:34px" role="img" aria-label="Paper flower"></div>
  <div class="art" style="left:356px;top:592px;width:215px;height:122px;border-radius:50% 50% 30% 30%;background:linear-gradient(180deg,var(--yellow),var(--orange) 60%,var(--red))" role="img" aria-label="Striped sombrero"></div>
  <div class="band band-bottom" role="img" aria-label="Zigzag stripe border"></div>
</section>

<section class="panel col-right row-3">
  <div class="band band-top" style="height:86px;background:linear-gradient(100deg,var(--purple) 0 10%,var(--pink) 30%,var(--yellow) 60%,var(--aqua) 85%)" role="img" aria-label="Sweeping retro colour swooshes"></div>
  <h2 class="section-title plain c-p" style="top:96px;font-size:22px;letter-spacing:.12em">DESSERTS</h2>

  <div class="item" style="left:86px;width:414px;top:146px"><div class="line"><span class="name c-p">SOPAPILLA</span><span class="rule"></span><span class="price">2.59</span></div><p class="desc c-a">Warm fried flour tortillas with cinnamon sugar</p></div>
  <div class="item" style="left:86px;width:414px;top:185px"><div class="line"><span class="name" style="color:var(--pink)">FRIED ICE CREAM</span><span class="rule"></span><span class="price">3.99</span></div></div>
  <div class="item" style="left:86px;width:414px;top:212px"><div class="line"><span class="name" style="color:var(--orange)">MEXICAN CHURROS</span><span class="rule"></span><span class="price">3.59</span></div></div>
  <div class="item" style="left:86px;width:414px;top:237px"><div class="line"><span class="name" style="color:var(--pink)">STRAWBERRY</span><span class="rule"></span><span class="price">3.29</span></div><p class="name" style="color:var(--pink)">CHIMICHANGA</p></div>
  <div class="item" style="left:86px;width:414px;top:281px"><div class="line"><span class="name" style="color:var(--pink)">FLAN</span><span class="rule"></span><span class="price">2.99</span></div><p class="desc c-a">Rich caramel<br>Mexican custard</p></div>

  <h2 class="section-title plain c-b" style="top:324px;font-size:22px;letter-spacing:.12em">BEVERAGES</h2>
  <div class="item" style="left:86px;width:414px;top:374px"><div class="line"><span class="name">MEXICAN BEER</span><span class="rule"></span><span class="price">3.99</span></div><p class="desc c-a">Tierrita, Dos Lunas Amber, Solana, Dos Lunas Lager,<br>Marea Negra, Solana Light, Marea Especial</p></div>
  <div class="item" style="left:86px;width:414px;top:425px"><div class="line"><span class="name">DOMESTIC BEERS</span><span class="rule"></span><span class="price">3.19</span></div><p class="desc c-a">Millbrook Lite, Millbrook Ultra, Bayfield, Bayfield Light,<br>Hollow Lite, Crestline, Light</p></div>
  <div class="item" style="left:86px;width:414px;top:477px"><p class="name">DRAFT BEER</p>
    <div class="line desc c-a"><span>Domestic 16 oz</span><span class="rule"></span><span class="price" style="font-size:13px">2.79</span></div>
    <div class="line desc c-a"><span>Pitcher</span><span class="rule"></span><span class="price" style="font-size:13px">8.99</span></div>
    <div class="line desc c-a"><span>Import 16 oz</span><span class="rule"></span><span class="price" style="font-size:13px">3.49</span></div>
    <div class="line desc c-a"><span>Pitcher</span><span class="rule"></span><span class="price" style="font-size:13px">11.99</span></div></div>
  <div class="item" style="left:86px;width:414px;top:557px"><div class="line"><span class="name">SOFT DRINKS, ETC</span><span class="rule"></span><span class="price">2.29</span></div><p class="desc c-a">Cola, Diet Cola, Lemon-Lime, Iced Tea, Coffee, Lemonade<br>Citrus Glow, Doc Spice (to go cup 50 oz)</p></div>
  <div class="item" style="left:86px;width:414px;top:607px"><div class="line"><span class="name">AGUAS FRES CAS</span><span class="rule"></span><span class="price">2.29</span></div></div>
  <div class="item" style="left:86px;width:414px;top:633px"><div class="line"><span class="name">SOFT DRINK TO GO No refills</span><span class="rule"></span><span class="price">1.49</span></div></div>
  <div class="item" style="left:86px;width:414px;top:659px"><div class="line"><span class="name">MEXICAN SOFT DRINKS BY THE BOTTLE</span><span class="rule"></span><span class="price">1.99</span></div><p class="name" style="color:var(--pink);font-size:13px">Cola Roja and Cantaritos</p></div>
  <div class="item" style="left:86px;width:380px;top:703px;display:flex;justify-content:space-between"><span><span class="name">MILK</span> &nbsp; &nbsp; <span class="price">2.49</span></span><span><span class="name">CHOCOLATE MILK</span> &nbsp; <span class="price">2.99</span></span></div>
  <div class="band" style="bottom:0;height:76px;background:linear-gradient(100deg,var(--pink) 0 30%,var(--orange) 55%,var(--yellow) 80%,var(--aqua))" role="img" aria-label="Sweeping retro colour swooshes"></div>
</section>

</body>
</html>
```